New Business Card Design Project

Use the flyer uploaded and website www.brightoakbuilders.com for inspiration.
List Our Services on Backside of business cards
Marcus Delling
Harborline Builders Inc.
Licensed General Contractors
858-471-6093

Contact Information for Business Card

Use the flyer uploaded and website www.brightoakbuilders.com for inspiration. List Our Services on Backside of business cards Marcus Delling Harborline Builders Inc. Licensed General Contractors 858-471-6093

```html
<!DOCTYPE html>
<html lang="en">
<head>
<meta charset="utf-8">
<title>Harborline Builders – Business Card</title>
<link rel="stylesheet" href="https://fonts.googleapis.com/css2?family=Open+Sans:ital,wght@0,400;0,600;0,700;1,700&display=swap">
<style>
  :root {
    --stage: #1c1c1e;
    --card: #202024;
    --card-back: #1d1d1f;
    --red: #ed1c24;
    --blue: #5b86d6;
    --white: #ffffff;
    --muted: #e6e6e6;
  }
  * { box-sizing: border-box; margin: 0; padding: 0; }
  html, body {
    width: 1200px; height: 780px; overflow: hidden;
    background: var(--stage);
    font-family: "Open Sans", Arial, sans-serif;
  }
  .stage {
    position: relative; width: 1200px; height: 780px;
  }
  .card {
    position: absolute; top: 230px;
    width: 560px; height: 320px;
    overflow: hidden;
    box-shadow: 0 14px 30px rgba(0,0,0,.45);
  }
  .card-front { left: 30px; background: var(--card); }
  .card-back { left: 610px; background: var(--card-back); }

  .front-wave { position: absolute; inset: 0; }

  .brand-name {
    position: absolute;
    color: var(--white);
    font-weight: 400;
    letter-spacing: 2px;
    text-transform: uppercase;
    white-space: nowrap;
  }
  .card-front .brand-name { left: 300px; top: 46px; font-size: 18px; }

  .holder-name {
    position: absolute; left: 38px; top: 40px;
    color: var(--red); font-size: 34px; font-weight: 700; line-height: 1;
  }
  .holder-title {
    position: absolute; left: 40px; top: 82px;
    color: var(--white); font-size: 14px;
  }
  .divider {
    position: absolute; left: 246px; top: 100px;
    width: 1.5px; height: 85px; background: var(--red);
  }
  .contact-list {
    position: absolute; left: 262px; top: 106px;
    list-style: none;
  }
  .contact-list li {
    display: flex; align-items: center; gap: 8px;
    color: var(--white); font-size: 14.5px; height: 26px;
  }
  .contact-list svg { width: 15px; height: 15px; flex: none; }
  .company-line {
    position: absolute; left: 60px; top: 268px;
    color: var(--white); font-size: 15px;
  }

  .card-back .brand-name {
    left: 0; right: 0; top: 50px; text-align: center; font-size: 22px;
  }
  .guarantee {
    position: absolute; left: 0; right: 0; top: 104px;
    text-align: center; font-weight: 700; font-style: italic; line-height: 1.25;
  }
  .guarantee .headline { color: var(--red); font-size: 13px; display: block; }
  .guarantee .subhead { color: var(--blue); font-size: 13px; display: block; }
  .rule {
    position: absolute; top: 121px; height: 2px; background: var(--blue);
  }
  .rule-left { left: 18px; width: 126px; }
  .rule-right { right: 18px; width: 126px; }
  .service-list {
    position: absolute; left: 0; right: 0; top: 170px;
    list-style: none; text-align: center;
  }
  .service-row {
    color: var(--muted); font-size: 11.5px; line-height: 26px;
    white-space: nowrap;
  }
  .service { display: inline-flex; align-items: center; gap: 3px; margin: 0 4px; }
  .service svg { width: 10px; height: 10px; }
</style>
</head>
<body>
<main class="stage">

  <section class="card card-front" aria-label="Business card front">
    <svg class="front-wave" viewBox="0 0 560 320" preserveAspectRatio="none" aria-hidden="true">
      <path d="M0 95 C150 210 330 255 560 250 L560 320 L0 320 Z" fill="var(--red)"/>
      <path d="M8 80 C155 193 335 238 545 236" fill="none" stroke="var(--blue)" stroke-width="4"/>
    </svg>

    <div class="brand-name">Harborline Builders</div>

    <h1 class="holder-name">Marcus Delling</h1>
    <p class="holder-title">Licensed General Contractors</p>

    <div class="divider"></div>

    <ul class="contact-list">
      <li>
        <svg viewBox="0 0 16 16" aria-hidden="true"><path d="M4 1.5l2.3 3-1.4 1.6c.8 1.9 2.2 3.3 4.1 4.1l1.6-1.4 3 2.3-1.3 2.4C6.9 13.7 2.3 9.1 1.6 3l2.4-1.5z" fill="var(--red)"/></svg>
        858-471-6093
      </li>
      <li>
        <svg viewBox="0 0 16 16" aria-hidden="true"><rect x="1" y="3" width="14" height="10" rx="1.2" fill="var(--red)"/><path d="M1.5 4l6.5 5 6.5-5" fill="none" stroke="var(--card)" stroke-width="1.3"/></svg>
        info@brightoakbuilders.com
      </li>
      <li>
        <svg viewBox="0 0 16 16" aria-hidden="true"><circle cx="8" cy="8" r="7" fill="var(--red)"/><path d="M1 8h14M8 1c-3 3.5-3 10.5 0 14M8 1c3 3.5 3 10.5 0 14" fill="none" stroke="var(--card)" stroke-width="1"/></svg>
        www.brightoakbuilders.com
      </li>
    </ul>

    <p class="company-line">Harborline Builders Inc.</p>
  </section>

  <section class="card card-back" aria-label="Business card back">
    <div class="brand-name">Harborline Builders</div>

    <div class="rule rule-left"></div>
    <div class="rule rule-right"></div>
    <p class="guarantee">
      <span class="headline">OUR SERVICES ARE 100% GUARANTEED</span>
      <span class="subhead">SPECIALIZING IN:</span>
    </p>

    <ul class="service-list">
      <li class="service-row">
        <span class="service"><svg viewBox="0 0 10 10" aria-hidden="true"><circle cx="5" cy="5" r="4.3" fill="none" stroke="var(--red)" stroke-width="1"/><path d="M2.8 5.2l1.5 1.5 3-3.2" fill="none" stroke="var(--red)" stroke-width="1.2"/></svg>Remodel: Kitchen &amp; Bath</span>
        <span class="service"><svg viewBox="0 0 10 10" aria-hidden="true"><circle cx="5" cy="5" r="4.3" fill="none" stroke="var(--red)" stroke-width="1"/><path d="M2.8 5.2l1.5 1.5 3-3.2" fill="none" stroke="var(--red)" stroke-width="1.2"/></svg>Painting: Interior &amp; Exterior</span>
        <span class="service"><svg viewBox="0 0 10 10" aria-hidden="true"><circle cx="5" cy="5" r="4.3" fill="none" stroke="var(--red)" stroke-width="1"/><path d="M2.8 5.2l1.5 1.5 3-3.2" fill="none" stroke="var(--red)" stroke-width="1.2"/></svg>Flooring: Carpet, Vinyl, Wood</span>
      </li>
      <li class="service-row">
        <span class="service"><svg viewBox="0 0 10 10" aria-hidden="true"><circle cx="5" cy="5" r="4.3" fill="none" stroke="var(--red)" stroke-width="1"/><path d="M2.8 5.2l1.5 1.5 3-3.2" fill="none" stroke="var(--red)" stroke-width="1.2"/></svg>Window &amp; Door Replacement</span>
        <span class="service"><svg viewBox="0 0 10 10" aria-hidden="true"><circle cx="5" cy="5" r="4.3" fill="none" stroke="var(--red)" stroke-width="1"/><path d="M2.8 5.2l1.5 1.5 3-3.2" fill="none" stroke="var(--red)" stroke-width="1.2"/></svg>Plumbing: Repairs &amp; Upgrades</span>
        <span class="service"><svg viewBox="0 0 10 10" aria-hidden="true"><circle cx="5" cy="5" r="4.3" fill="none" stroke="var(--red)" stroke-width="1"/><path d="M2.8 5.2l1.5 1.5 3-3.2" fill="none" stroke="var(--red)" stroke-width="1.2"/></svg>Energy-Efficient Upgrades</span>
      </li>
      <li class="service-row">
        <span class="service"><svg viewBox="0 0 10 10" aria-hidden="true"><circle cx="5" cy="5" r="4.3" fill="none" stroke="var(--red)" stroke-width="1"/><path d="M2.8 5.2l1.5 1.5 3-3.2" fill="none" stroke="var(--red)" stroke-width="1.2"/></svg>Deck &amp; Patio Construction</span>
        <span class="service"><svg viewBox="0 0 10 10" aria-hidden="true"><circle cx="5" cy="5" r="4.3" fill="none" stroke="var(--red)" stroke-width="1"/><path d="M2.8 5.2l1.5 1.5 3-3.2" fill="none" stroke="var(--red)" stroke-width="1.2"/></svg>Water &amp; Mold Damage</span>
        <span class="service"><svg viewBox="0 0 10 10" aria-hidden="true"><circle cx="5" cy="5" r="4.3" fill="none" stroke="var(--red)" stroke-width="1"/><path d="M2.8 5.2l1.5 1.5 3-3.2" fill="none" stroke="var(--red)" stroke-width="1.2"/></svg>Garage Renovation</span>
      </li>
    </ul>
  </section>

</main>
</body>
</html>
```